Redesign of business card for Cedar Ridge Mechanical

We are looking for a new design for our business cards for Cedar Ridge Mechanical. We are a plumbing & HVAC construction company, operating on the West Coast of Canada and USA. Logo attached.
Industry/Entity Type
Construction - Plumbing & HVAC
Contact Information for Business Card
Name, address, phone numbers, email, website address
Look and feel
Each slider illustrates characteristics of the customer's brand and the style your logo design should communicate.

```html
<!DOCTYPE html>
<html lang="en">
<head>
<meta charset="UTF-8">
<title>Cedar Ridge Mechanical — Business Card</title>
<link rel="stylesheet" href="https://fonts.googleapis.com/css2?family=Jost:wght@400;500;700&display=swap">
<style>
  :root {
    --page-bg: #e9e6e1;
    --front-light: #4b4b4e;
    --front-dark: #1b1b1c;
    --front-mark: #3a3a3d;
    --back-dark: #161c26;
    --back-mid: #3e4859;
    --back-edge: #0f131a;
    --ink-navy: #0d1420;
    --ink-white: #f2f4f7;
    --ink-soft: #d3d8df;
    --mark-navy: #141a24;
  }
  * { box-sizing: border-box; margin: 0; padding: 0; }
  html, body { width: 1200px; height: 900px; overflow: hidden; }
  body {
    background: var(--page-bg);
    font-family: "Jost", sans-serif;
    position: relative;
  }
  .card {
    position: absolute;
    width: 665px;
    height: 380px;
    border-radius: 48px 8px 48px 8px;
    box-shadow: 0 12px 30px rgba(0,0,0,0.25);
    overflow: hidden;
  }
  /* Front */
  .card--front {
    left: 150px; top: 46px;
    background: linear-gradient(115deg, var(--front-light) 0%, #2c2c2e 45%, var(--front-dark) 100%);
  }
  .front__url {
    position: absolute;
    top: 34px; right: 40px;
    color: var(--ink-white);
    font-size: 17px;
    font-weight: 500;
    letter-spacing: 0.42em;
  }
  .front__mark {
    position: absolute;
    left: 48px; top: 150px;
    display: flex;
    align-items: center;
    gap: 22px;
  }
  .front__square {
    width: 70px; height: 70px;
    background: var(--front-mark);
    border-radius: 6px;
  }
  .front__name {
    color: var(--front-mark);
    font-size: 44px;
    font-weight: 700;
    line-height: 1.05;
    text-transform: uppercase;
  }
  /* Back */
  .card--back {
    left: 385px; top: 474px;
    background: linear-gradient(100deg, var(--back-dark) 0%, #2a3342 35%, var(--back-mid) 58%, #242c39 78%, var(--back-edge) 100%);
  }
  .back__person {
    position: absolute;
    left: 42px; top: 92px;
  }
  .back__name {
    color: var(--ink-navy);
    font-size: 22px;
    font-weight: 700;
    text-transform: uppercase;
    letter-spacing: 0.02em;
  }
  .back__title {
    color: var(--ink-white);
    font-size: 17px;
    margin-top: 2px;
  }
  .back__contacts {
    position: absolute;
    left: 42px; top: 176px;
    list-style: none;
    color: var(--ink-white);
    font-size: 18px;
  }
  .back__contacts li {
    display: flex;
    align-items: center;
    gap: 10px;
    height: 27px;
  }
  .back__contacts svg { width: 15px; height: 15px; flex: none; }
  .back__address {
    position: absolute;
    left: 42px; top: 280px;
    color: var(--ink-white);
    font-size: 18px;
    line-height: 1.3;
    font-style: normal;
  }
  .back__mark {
    position: absolute;
    right: 40px; top: 120px;
    display: flex;
    align-items: center;
    gap: 14px;
  }
  .back__square {
    width: 40px; height: 40px;
    background: var(--mark-navy);
    border-radius: 4px;
  }
  .back__brand {
    color: var(--mark-navy);
    font-size: 24px;
    font-weight: 700;
    line-height: 1.1;
    text-transform: uppercase;
  }
</style>
</head>
<body>
  <section class="card card--front" aria-label="Card front">
    <p class="front__url">www.cedarridgemech.com</p>
    <div class="front__mark">
      <span class="front__square"></span>
      <span class="front__name">Cedar Ridge<br>Mechanical</span>
    </div>
  </section>

  <section class="card card--back" aria-label="Card back">
    <div class="back__person">
      <p class="back__name">Martin Calloway</p>
      <p class="back__title">President/Founder</p>
    </div>
    <ul class="back__contacts">
      <li>
        <svg viewBox="0 0 16 16" aria-hidden="true"><path d="M4 1.5l2.3 3-1.4 1.6a8 8 0 0 0 5 5l1.6-1.4 3 2.3-1.5 2.5C7.5 14.5 1.5 8.5 1.5 3z" fill="#f2f4f7"/></svg>
        213-555-0148
      </li>
      <li>
        <svg viewBox="0 0 16 16" aria-hidden="true"><rect x="1" y="3" width="14" height="10" rx="1" fill="#f2f4f7"/><path d="M1.5 3.5L8 9l6.5-5.5" fill="none" stroke="#2a3342" stroke-width="1.3"/></svg>
        info@cedarridgemech.com
      </li>
      <li>
        <svg viewBox="0 0 16 16" aria-hidden="true"><g fill="none" stroke="#f2f4f7" stroke-width="1.2"><circle cx="8" cy="8" r="6.5"/><ellipse cx="8" cy="8" rx="3" ry="6.5"/><path d="M1.5 8h13M2.5 4.8h11M2.5 11.2h11"/></g></svg>
        www.cedarridgemech.com
      </li>
    </ul>
    <address class="back__address">2750 Harbor View Rd. S,<br>Suite #410 Tacoma, WA 98402</address>
    <div class="back__mark">
      <span class="back__square"></span>
      <span class="back__brand">Cedar Ridge<br>Mechanical</span>
    </div>
  </section>
</body>
</html>
```